Roofing company in Toronto, Canada needs a logo design and business card design

We need a business card and logo created for our company. Our company is "KLV Roofing" which provides roofing services for commercial and residential customers. We serve customers in the Greater Toronto Area (in Canada) thus the name KLV.

We want the logo and business card to be a modern design displaying professionalism and quality in the work. We would prefer rounded corners for the business cards but are open to other ideas. The cards should be pleasant and appealing to customers.

Target Market(s)

Commercial and Residential customers

Industry/Entity Type

Roofing

Contact Information for Business Card

Logo Text

KLV Roofing

Requirements
Nice to have
• Colours that are pleasing to the eye but at the same time should stand out from other business cards. If the design can incorporate the name of KLV Roofing and the actual concept of roofing that would be nice.
Should not have
• Do not want the business cards or logo to be childish looking. Need to look professionally designed.

```html
<!DOCTYPE html>
<html lang="en">
<head>
<meta charset="utf-8">
<title>KLV Roofing – Business Card</title>
<link rel="stylesheet" href="https://fonts.googleapis.com/css2?family=Lato:wght@400;700;900&display=swap">
<style>
  :root {
    --page-bg: #e3e5e9;
    --card-bg: #eef0f3;
    --brand-blue: #2a5caa;
    --brand-grey: #3b3d42;
    --text-dark: #33353a;
    --text-light: #d3d6db;
  }
  html, body {
    margin: 0;
    padding: 0;
    width: 1200px;
    height: 970px;
    overflow: hidden;
    background: var(--page-bg);
    font-family: "Lato", sans-serif;
  }
  .card {
    position: absolute;
    left: 80px;
    top: 189px;
    width: 1040px;
    height: 592px;
    background: var(--card-bg);
    overflow: hidden;
    box-shadow: 0 10px 30px rgba(0,0,0,0.18);
  }
  .card-shapes {
    position: absolute;
    inset: 0;
  }
  .logo {
    position: absolute;
    left: 672px;
    top: 150px;
    display: flex;
    align-items: center;
    gap: 14px;
  }
  .logo-mark {
    width: 30px;
    height: 30px;
    background: var(--brand-blue);
  }
  .logo-name {
    font-weight: 900;
    font-size: 50px;
    color: var(--brand-grey);
    letter-spacing: 1px;
    white-space: nowrap;
  }
  .person {
    position: absolute;
    left: 50px;
    top: 243px;
  }
  .person-name {
    font-weight: 700;
    font-size: 36px;
    color: var(--text-dark);
    line-height: 1;
  }
  .person-title {
    font-size: 27px;
    color: var(--brand-blue);
    line-height: 1.1;
  }
  .address {
    position: absolute;
    left: 50px;
    top: 334px;
    font-size: 26px;
    line-height: 35px;
    color: var(--text-dark);
  }
  .contact-list {
    position: absolute;
    left: 50px;
    top: 413px;
    margin: 0;
    padding: 0;
    list-style: none;
    font-size: 26px;
    line-height: 37px;
    color: var(--text-dark);
  }
  .contact-list li {
    display: flex;
    align-items: center;
    gap: 10px;
  }
  .contact-icon {
    width: 28px;
    height: 28px;
    flex: none;
  }
  .website {
    position: absolute;
    left: 655px;
    top: 525px;
    font-size: 24px;
    color: var(--text-light);
  }
</style>
</head>
<body>
  <div class="card">
    <svg class="card-shapes" width="1040" height="592" viewBox="0 0 1040 592">
      <path d="M0,0 H1040 V14 C 620,8 240,40 0,225 Z" fill="var(--brand-blue)"/>
      <path d="M0,592 V552 C 450,565 900,420 1040,235 V592 Z" fill="var(--brand-grey)"/>
    </svg>

    <div class="logo">
      <span class="logo-mark"></span>
      <span class="logo-name">KLV Roofing</span>
    </div>

    <div class="person">
      <div class="person-name">DANIEL REYES</div>
      <div class="person-title">Managing Director</div>
    </div>

    <div class="address">
      PO BOX 456 Maple Avenue<br>
      Unit 2, Toronto, Canada
    </div>

    <ul class="contact-list">
      <li>
        <svg class="contact-icon" viewBox="0 0 28 28" aria-hidden="true">
          <rect width="28" height="28" fill="var(--brand-blue)"/>
          <path d="M7 11 Q14 5 21 11 L19 13 L17 11 L11 11 L9 13 Z M9 14 H19 L20 21 H8 Z" fill="#fff"/>
          <circle cx="14" cy="17" r="2" fill="var(--brand-blue)"/>
        </svg>
        <span>(01) 4821 5530</span>
      </li>
      <li>
        <svg class="contact-icon" viewBox="0 0 28 28" aria-hidden="true">
          <rect width="28" height="28" fill="var(--brand-blue)"/>
          <rect x="9" y="6" width="10" height="5" fill="#fff"/>
          <rect x="6" y="12" width="16" height="7" fill="#fff"/>
          <rect x="9" y="17" width="10" height="5" fill="#fff" stroke="var(--brand-blue)" stroke-width="1"/>
        </svg>
        <span>(01) 4821 5530</span>
      </li>
      <li>
        <svg class="contact-icon" viewBox="0 0 28 28" aria-hidden="true">
          <rect width="28" height="28" fill="var(--brand-blue)"/>
          <rect x="6" y="8" width="16" height="12" fill="none" stroke="#fff" stroke-width="1.6"/>
          <path d="M6 8 L14 15 L22 8 M6 20 L12 14 M22 20 L16 14" fill="none" stroke="#fff" stroke-width="1.6"/>
        </svg>
        <span>info@klvroofing.ca</span>
      </li>
    </ul>

    <div class="website">www.klvroofing.ca</div>
  </div>
</body>
</html>
```